TLK Electricial Contracting Services

Hi guys, after a design for my small electrical company, have logo design files to be incorporated into the layout, the basic concept is electrical contracting services for residential, commercial, industrial & data services, image is clean clear and strong,

Card format is to have a nice clean logo on front,with maybe the Residential – commercial – industrial - data, followed with licensed & insured, followed by contact details on backside of the card.

Target Market(s)

Residential, commercial, industrial sectors.

Industry/Entity Type

Electrical

Contact Information for Business Card

TLK logo,
Residential – commercial – industrial - data
REC: 61307
Email: tlk@vornamail.net.au
Phone: 0487 352 019

Requirements
Must have
• Clean & strong design.
Nice to have
• If possible, I would like the logo colours inverted so the text is orange and the background is black on the front of the card, then the backside of the card be the reverse colour
Should not have
• No Sparks, lightning bolts,

```html
<!DOCTYPE html>
<html lang="en">
<head>
<meta charset="utf-8">
<title>TLK Electrical – Business Cards</title>
<link rel="stylesheet" href="https://fonts.googleapis.com/css2?family=Michroma&display=swap">
<style>
  :root {
    --backdrop: #ececec;
    --orange: #ee8636;
    --ink: #232323;
    --card-w: 500px;
    --card-h: 305px;
  }
  * { box-sizing: border-box; margin: 0; padding: 0; }
  html, body {
    width: 1200px; height: 800px; overflow: hidden;
    background: var(--backdrop);
    font-family: "Michroma", "Arial", sans-serif;
  }
  .canvas { position: relative; width: 1200px; height: 800px; }

  .card {
    position: absolute;
    width: var(--card-w); height: var(--card-h);
    box-shadow: 0 6px 14px rgba(0,0,0,0.12);
  }
  .card--contact { left: 90px; top: 110px; background: var(--orange); color: var(--ink); }
  .card--services { left: 610px; top: 385px; background: var(--ink); color: var(--orange); }

  .rec { position: absolute; top: 26px; right: 30px; font-size: 10px; letter-spacing: 0.5px; }

  .brand { position: absolute; left: 34px; }
  .card--contact .brand { top: 70px; }
  .card--services .brand { top: 48px; }
  .brand__name { font-size: 62px; line-height: 1; letter-spacing: -1px; }
  .brand__line { font-size: 11px; margin-top: 6px; letter-spacing: 0.3px; }

  .contacts { position: absolute; left: 34px; top: 190px; list-style: none; }
  .contacts li { display: flex; align-items: center; gap: 12px; margin-bottom: 12px; }
  .contacts svg { width: 20px; height: 20px; fill: var(--ink); }
  .contacts__phone { font-size: 17px; letter-spacing: 1px; }
  .contacts__email { font-size: 13px; }

  .services {
    position: absolute; left: 34px; bottom: 34px;
    font-size: 25px; line-height: 1.3; letter-spacing: 0.3px;
  }
</style>
</head>
<body>
<main class="canvas">
  <section class="card card--contact" aria-label="Card back – contact details">
    <p class="rec">REC. 61307</p>
    <div class="brand">
      <p class="brand__name">TLK</p>
      <p class="brand__line">Tavin Kole Electrical</p>
    </div>
    <ul class="contacts">
      <li>
        <svg viewBox="0 0 24 24" aria-hidden="true"><path d="M6.6 10.8a15.1 15.1 0 0 0 6.6 6.6l2.2-2.2a1 1 0 0 1 1-.25 11.4 11.4 0 0 0 3.6.57 1 1 0 0 1 1 1V20a1 1 0 0 1-1 1A17 17 0 0 1 3 4a1 1 0 0 1 1-1h3.5a1 1 0 0 1 1 1c0 1.25.2 2.45.57 3.6a1 1 0 0 1-.25 1z"/></svg>
        <span class="contacts__phone">0487 352 019</span>
      </li>
      <li>
        <svg viewBox="0 0 24 24" aria-hidden="true"><path d="M2 5h20v14H2z M3.5 6.5 12 13l8.5-6.5" fill="none" stroke="#232323" stroke-width="2"/></svg>
        <span class="contacts__email">tlk@vornamail.net.au</span>
      </li>
    </ul>
  </section>

  <section class="card card--services" aria-label="Card front – services">
    <p class="rec">REC. 61307</p>
    <div class="brand">
      <p class="brand__name">TLK</p>
      <p class="brand__line">Tavin Kole Electrical</p>
    </div>
    <p class="services">Residential, Commercial<br>Industrial &amp; Data Services</p>
  </section>
</main>
</body>
</html>
```